Designer Instructions – Updated Referral Program Flyer

(Based on the mock-up in “Brief Layout and Instructions.pdf”)

OVERALL STYLE + LAYOUT

Maintain the same general layout, structure, and flow as the mock-up flyer (front and back).

This is an update of an older flyer, not a full redesign — keep the same sections, proportions, and overall visual feel, but with cleaner, more modern design improvements.

The final flyer should look clean, bold, professional, and high-impact, geared toward realtors, property managers, and contractors who refer work.

FRONT SIDE INSTRUCTIONS
1. Header Section

Remove the Rebuild Harbor Crest logo from the top banner.
(Shown on page 1 of the PDF)

2. Main Headline

Keep the same three-line structure:
EARN
UNLIMITED
CASH

Center it, maximize impact, and increase the font size of CASH so all three words match in importance.

Make the headline bold, clean, and the main focal point.

3. Cash Incentive Box

Keep the "$500 minimum OR 10% per referral" box, but upgrade the graphics to look sharper and more modern.

Ensure the wording matches exactly what’s in the mock-up.

4. Premier Partner Program Ribbon

Clean up and modernize the "PREMIER PARTNER PROGRAM" bar while keeping the same position and structure.

Ensure the checkmark badge remains crisp and professional.

5. Supporting Icons Section

Keep the four icons/benefit boxes (Guaranteed Payout, Free Evaluations, Affordable Solutions, Industry Leaders) in the same order.

Update the icons to cleaner, more modern styles — but maintain the same meanings.

Improve alignment and spacing for sharper visual consistency.

6. Remove Icons in Contact Area

At the bottom (“CALL TEXT OR BOOK ONLINE 858-471-6093 BrightlaneRenovate.com”), remove the phone and internet icons, as noted on page 2 of the PDF.

7. Replace All Images

I (Dorian) will provide all updated stock images separately via email.

Replace the flood/water-damage imagery and roof leak with the new images I send.

Keep image placement and proportions the same as the mock-up.

BACK SIDE INSTRUCTIONS
1. Header Image + “REFER / EARN” Section

Maintain the same large split-image layout (“The more you refer, the more you earn”).

Replace all background imagery with the new assets I will send.

Keep the CASH FLOW image section but modernize the type and spacing.

2. “HOW IT WORKS” Section

Preserve the three-column layout:

Refer Flood, Water & Mold Damage

We Take Care of Everything (evaluations/insurance)

Get Paid to Share

Update images, tighten spacing, and use modern iconography.

3. Remove Phone/Internet Icons

Same as the front side — remove small communication icons and keep only the text/number/URL.

4. Bottom Contact Bar

Keep the blue bar, same wording, same layout — just modernize the style if needed for clarity.

5. Replace All Back-Side Images

Again, I will email you the image assets.

Keep the layout EXACT — just update with higher-quality photos and improved design.

TEXT CONTENT (Keep as-is unless spacing adjustments needed)

All text shown in the PDF should remain exactly the same unless spacing or visual balance requires minor adjustments.
Example from page 3:

“REFER FLOOD, MOLD & CONSTRUCTION JOBS”

“We Schedule a Free Estimate. If Approved, You Get Paid.”

“Everybody Benefits From Referrals”

Everything stays, just refreshed and visually improved.

DESIGN GOALS

Flyer should look high-end and trustworthy, not salesy.

Consistent color theme: blues, whites, yellows, same palette as original.

Use bold, modern fonts with strong readability.

Ensure all headlines pop and all benefit boxes are clean, well-aligned, and evenly spaced.

The final result should feel like a premium referral program flyer for a top-tier restoration/remodel company.

FILES I WILL PROVIDE

I will send the designer:

All replacement stock photos

Any updated logos (if needed)

Original high-resolution version of the mock-up (if available)

Any additional icons preferred

Colors
0054AA
0677BA
7BADD7
CADEEF
E8F1F8

Requirements
Must have
• Designer Instructions – Updated Referral Program Flyer (Based on the mock-up in “Brief Layout and Instructions.pdf”) OVERALL STYLE + LAYOUT Maintain the same general layout, structure, and flow as the mock-up flyer (front and back). This is an update of an older flyer, not a full redesign — keep the same sections, proportions, and overall visual feel, but with cleaner, more modern design improvements. The final flyer should look clean, bold, professional, and high-impact, geared toward realtors, property managers, and contractors who refer work. FRONT SIDE INSTRUCTIONS 1. Header Section Remove the Rebuild Harbor Crest logo from the top banner. (Shown on page 1 of the PDF) 2. Main Headline Keep the same three-line structure: EARN UNLIMITED CASH Center it, maximize impact, and increase the font size of CASH so all three words match in importance. Make the headline bold, clean, and the main focal point. 3. Cash Incentive Box Keep the "$500 minimum OR 10% per referral" box, but upgrade the graphics to look sharper and more modern. Ensure the wording matches exactly what’s in the mock-up. 4. Premier Partner Program Ribbon Clean up and modernize the "PREMIER PARTNER PROGRAM" bar while keeping the same position and structure. Ensure the checkmark badge remains crisp and professional. 5. Supporting Icons Section Keep the four icons/benefit boxes (Guaranteed Payout, Free Evaluations, Affordable Solutions, Industry Leaders) in the same order. Update the icons to cleaner, more modern styles — but maintain the same meanings. Improve alignment and spacing for sharper visual consistency. 6. Remove Icons in Contact Area At the bottom (“CALL TEXT OR BOOK ONLINE 858-471-6093 BrightlaneRenovate.com”), remove the phone and internet icons, as noted on page 2 of the PDF. 7. Replace All Images I (Dorian) will provide all updated stock images separately via email. Replace the flood/water-damage imagery and roof leak with the new images I send. Keep image placement and proportions the same as the mock-up. BACK SIDE INSTRUCTIONS 1. Header Image + “REFER / EARN” Section Maintain the same large split-image layout (“The more you refer, the more you earn”). Replace all background imagery with the new assets I will send. Keep the CASH FLOW image section but modernize the type and spacing. 2. “HOW IT WORKS” Section Preserve the three-column layout: Refer Flood, Water & Mold Damage We Take Care of Everything (evaluations/insurance) Get Paid to Share Update images, tighten spacing, and use modern iconography. 3. Remove Phone/Internet Icons Same as the front side — remove small communication icons and keep only the text/number/URL. 4. Bottom Contact Bar Keep the blue bar, same wording, same layout — just modernize the style if needed for clarity. 5. Replace All Back-Side Images Again, I will email you the image assets. Keep the layout EXACT — just update with higher-quality photos and improved design. TEXT CONTENT (Keep as-is unless spacing adjustments needed) All text shown in the PDF should remain exactly the same unless spacing or visual balance requires minor adjustments. Example from page 3: “REFER FLOOD, MOLD & CONSTRUCTION JOBS” “We Schedule a Free Estimate. If Approved, You Get Paid.” “Everybody Benefits From Referrals” Everything stays, just refreshed and visually improved. DESIGN GOALS Flyer should look high-end and trustworthy, not salesy. Consistent color theme: blues, whites, yellows, same palette as original. Use bold, modern fonts with strong readability. Ensure all headlines pop and all benefit boxes are clean, well-aligned, and evenly spaced. The final result should feel like a premium referral program flyer for a top-tier restoration/remodel company. FILES I WILL PROVIDE I will send the designer: All replacement stock photos Any updated logos (if needed) Original high-resolution version of the mock-up (if available) Any additional icons preferred

```html
<!DOCTYPE html>
<html lang="en">
<head>
<meta charset="utf-8">
<title>Referral Partner Program Flyer</title>
<link href="https://fonts.googleapis.com/css2?family=Poppins:wght@400;500;600;700;800&family=Anton&display=swap" rel="stylesheet">
<style>
:root{
  --stage:#c4c4c4;
  --white:#ffffff;
  --navy:#0f2a5e;
  --navy-deep:#0a1a33;
  --panel-navy:#1c3f7e;
  --blue:#3d87f0;
  --blue-bar:#4a8ff0;
  --sky:#7badd7;
  --yellow:#ffe01a;
  --red:#e8202a;
  --red-deep:#c60c12;
  --ink:#14213a;
}
*{margin:0;padding:0;box-sizing:border-box}
html,body{width:899px;height:1200px;overflow:hidden;background:var(--stage);font-family:"Poppins",sans-serif}
.flyer{position:absolute;left:111px;width:678px;height:439px;background:var(--white);overflow:hidden;box-shadow:0 6px 14px rgba(0,0,0,.28)}
.flyer--front{top:119px}
.flyer--back{top:643px}
.abs{position:absolute}

/* front headline */
.headline{left:20px;top:14px;font-weight:800;line-height:1;letter-spacing:-1px}
.headline__earn{display:block;font-size:66px;color:var(--blue)}
.headline__unlimited{display:block;font-size:34px;color:var(--navy);margin-top:2px}
.headline__cash{display:block;font-size:68px;color:var(--navy);margin-top:2px}

.hero-photo{left:0;top:0;width:678px;height:216px;background:linear-gradient(160deg,#eef0f2 0%,#d9dde1 40%,#c9b79e 80%,#a8906f 100%);clip-path:polygon(357px 0,678px 0,678px 216px,330px 216px,290px 140px)}
.seal{left:279px;top:110px;width:70px;height:70px;border-radius:50%;background:var(--red);border:4px solid var(--white);box-shadow:0 0 0 2px var(--red)}

.flood-band{left:0;top:186px;width:540px;height:44px;background:var(--yellow);clip-path:polygon(0 0,500px 0,540px 44px,0 44px);font-weight:800;font-size:26px;color:var(--ink);line-height:44px;padding-left:20px;letter-spacing:-.3px}
.cash-band{left:0;top:229px;width:400px;height:43px;background:var(--red);display:flex;align-items:center;padding-left:30px;color:var(--white);font-weight:800}
.cash-band__big{font-size:40px;line-height:1;letter-spacing:-1px}
.cash-band__big sup{font-size:20px;vertical-align:top;position:relative;top:2px}
.cash-band__small{color:var(--yellow);font-size:16px;line-height:.85;margin-left:6px;font-weight:800}
.cash-band__or{width:34px;height:34px;border-radius:50%;background:var(--blue);border:2px solid var(--white);display:flex;align-items:center;justify-content:center;font-size:14px;font-weight:600;margin:0 12px 0 12px}
.cash-band__per{font-size:14px;line-height:.9;margin-left:6px}

.premier{left:423px;top:220px;width:235px;text-align:center;color:var(--red);font-weight:800;font-size:21px;letter-spacing:.3px}
.partner-pill{left:423px;top:244px;width:235px;height:28px;background:var(--yellow);border-radius:3px;display:flex;align-items:center;justify-content:center;gap:10px;font-weight:800;font-size:18px;color:var(--ink)}

.benefits{left:0;top:288px;width:678px;height:94px}
.benefit{position:absolute;top:288px;width:150px;color:var(--ink)}
.benefit__title{font-weight:700;font-size:11.5px;line-height:1.25;margin-top:12px}
.benefit__body{font-size:8.6px;line-height:1.25;margin-top:6px;width:82px}

.contact-bar{left:0;bottom:0;width:678px;height:42px}
.contact-bar__cta{position:absolute;left:24px;top:0;line-height:42px;color:var(--white);font-weight:700;font-size:16.5px}
.contact-bar__phone{position:absolute;left:300px;top:0;line-height:42px;color:var(--navy);font-weight:700;font-size:17px}
.contact-bar__sep{position:absolute;left:431px;top:14px;width:1px;height:14px;background:#9aa6b8}
.contact-bar__web{position:absolute;left:440px;top:0;line-height:42px;color:var(--navy);font-weight:700;font-size:14px}

/* back */
.back-hero{left:0;top:0;width:678px;height:242px}
.money-photo{left:0;top:0;width:678px;height:242px;background:linear-gradient(135deg,#b9bfb8 0%,#e7e9e2 35%,#c7ccc3 60%,#8f958c 100%);clip-path:polygon(323px 0,678px 0,678px 242px,240px 242px)}

.how-title{left:26px;top:263px;font-weight:800;font-size:33px;line-height:1.15;letter-spacing:-.5px}
.how-title span{display:block}
.how-title__a{color:var(--navy)}
.how-title__b{color:var(--blue)}
.step{position:absolute;top:252px;width:156px;height:107px;border-radius:4px;overflow:hidden;background:var(--panel-navy);text-align:center;color:var(--white)}
.step__photo{height:51px}
.step__title{font-weight:700;font-size:10.3px;line-height:1.3;margin-top:4px}
.step__body{font-size:6.8px;line-height:1.3;margin-top:4px}

.refer-row{left:24px;top:373px;width:633px;height:21px;border:1px solid #e3a3a3;display:flex;align-items:center}
.refer-row__label{width:147px;height:21px;margin-left:-1px;background:var(--red-deep);border-radius:9px 0 0 9px;color:var(--white);font-weight:500;font-size:16px;text-align:center;line-height:21px}
.refer-row__items{display:flex;justify-content:space-around;flex:1;font-size:15px;font-weight:500;color:var(--ink)}
.refer-row__items span{display:flex;align-items:center;gap:4px}
.tick{width:12px;height:12px}
</style>
</head>
<body>

<!-- FRONT -->
<section class="flyer flyer--front">
  <div class="abs hero-photo" role="img" aria-label="Photo of a bright renovated white kitchen with pendant light and wood floor"></div>
  <svg class="abs" style="left:0;top:0" width="678" height="216">
    <polyline points="357,0 276,103 303,139" fill="none" stroke="var(--blue)" stroke-width="6"/>
  </svg>
  <div class="abs seal" role="img" aria-label="24 hour emergency service seal"></div>

  <h1 class="abs headline">
    <span class="headline__earn">EARN</span>
    <span class="headline__unlimited">UNLIMITED</span>
    <span class="headline__cash">CA$H</span>
  </h1>

  <svg class="abs" style="left:500px;top:216px" width="45" height="14"><polygon points="0,0 45,0 40,14" fill="#c9a90f"/></svg>
  <div class="abs flood-band">GET PET TO REFFER A FLOOD</div>
  <div class="abs cash-band">
    <span class="cash-band__big"><sup>$</sup>500</span>
    <span class="cash-band__small">MINI<br>MUM</span>
    <span class="cash-band__or">OR</span>
    <span class="cash-band__big">10%</span>
    <span class="cash-band__small cash-band__per">PER<br>REFERRAL</span>
  </div>

  <div class="abs premier">PREMIER</div>
  <div class="abs partner-pill">
    <span>PARTNER</span>
    <svg width="22" height="22" viewBox="0 0 22 22"><circle cx="11" cy="11" r="10" fill="var(--blue)"/><polyline points="6,11 10,15 16,7" fill="none" stroke="#fff" stroke-width="2.4"/></svg>
    <span>PROGRAM</span>
  </div>

  <svg class="abs benefits" viewBox="0 0 678 94">
    <g fill="none" stroke-width="1.2" stroke="var(--sky)">
      <line x1="22" y1="2" x2="165" y2="2"/><line x1="22" y1="91" x2="165" y2="91"/>
      <line x1="178" y1="2" x2="322" y2="2"/><line x1="178" y1="91" x2="322" y2="91"/>
      <line x1="334" y1="2" x2="478" y2="2"/><line x1="334" y1="91" x2="478" y2="91"/>
      <line x1="490" y1="2" x2="633" y2="2"/><line x1="490" y1="91" x2="633" y2="91"/>
    </g>
    <g fill="none" stroke-width="6">
      <polyline points="165,2 177,46 165,91" stroke="var(--blue)"/>
      <polyline points="322,2 334,46 322,91" stroke="var(--navy)"/>
      <polyline points="478,2 490,46 478,91" stroke="var(--blue)"/>
      <polyline points="634,2 646,46 634,91" stroke="var(--navy)"/>
    </g>
    <g fill="none" stroke="var(--blue)" stroke-width="1.4">
      <circle cx="147" cy="38" r="13"/><polyline points="141,38 146,43 153,33"/><polyline points="139,49 134,62 141,59 144,64 147,52"/><polyline points="155,49 160,62 153,59 150,64 147,52"/>
    </g>
    <g fill="none" stroke="var(--navy)" stroke-width="1.4">
      <rect x="294" y="28" width="20" height="28" rx="2"/><line x1="298" y1="40" x2="310" y2="40"/><line x1="298" y1="45" x2="306" y2="45"/><rect x="305" y="42" width="15" height="20" rx="1"/><line x1="308" y1="47" x2="317" y2="47"/><circle cx="301" cy="33" r="3"/>
    </g>
    <g fill="none" stroke="var(--blue)" stroke-width="1.4">
      <circle cx="460" cy="34" r="8"/><line x1="457" y1="43" x2="463" y2="43"/><line x1="458" y1="46" x2="462" y2="46"/><path d="M440 58 q8 -8 16 -2 h8 q4 0 6 -4 l4 -2"/><path d="M440 64 q10 -2 16 0 q8 2 18 -10"/>
    </g>
    <g fill="none" stroke="var(--navy)" stroke-width="1.4">
      <circle cx="615" cy="30" r="8"/><circle cx="615" cy="30" r="3"/><circle cx="603" cy="50" r="3.5"/><path d="M597 62 q6 -10 12 0z"/><circle cx="617" cy="48" r="3.5"/><path d="M611 60 q6 -10 12 0z"/><circle cx="630" cy="50" r="3.5"/><path d="M624 62 q6 -10 12 0z"/>
    </g>
  </svg>
  <div class="benefit" style="left:31px">
    <div class="benefit__title">GUARANTEED<br>PAYOUT</div>
    <div class="benefit__body" style="width:88px">Minimum $500 or 10% of Total Invoice Paid Fast</div>
  </div>
  <div class="benefit" style="left:200px">
    <div class="benefit__title">FREE<br>ESTIMATES</div>
    <div class="benefit__body" style="width:90px">Fast &amp; Free Inspections &amp; Written Estimates</div>
  </div>
  <div class="benefit" style="left:356px">
    <div class="benefit__title">AFFORDABLE<br>SOLUTIONS</div>
    <div class="benefit__body" style="width:80px">Lowest Out of Pocket Costs for Your Customers</div>
  </div>
  <div class="benefit" style="left:513px">
    <div class="benefit__title">INDUSTRY<br>LEADERS</div>
    <div class="benefit__body" style="width:86px">Licensed &amp; Certified Experts Provide 100% Guarantee</div>
  </div>

  <div class="abs contact-bar">
    <svg class="abs" style="left:0;top:0" width="678" height="42">
      <polygon points="0,0 270,0 296,42 0,42" fill="var(--blue-bar)"/>
      <polyline points="270,0 296,40 678,40" fill="none" stroke="var(--navy)" stroke-width="3"/>
    </svg>
    <span class="contact-bar__cta">CALL, TEXT OR BOOK ONLINE</span>
    <span class="contact-bar__phone">858-471-6093</span>
    <span class="contact-bar__sep"></span>
    <span class="contact-bar__web">www.BrightlaneRenovate.com</span>
  </div>
</section>

<!-- BACK -->
<section class="flyer flyer--back">
  <svg class="abs back-hero" viewBox="0 0 678 242">
    <defs>
      <linearGradient id="goldFill" x1="0" y1="0" x2="1" y2="1">
        <stop offset="0" stop-color="#fff21a"/><stop offset=".55" stop-color="#ffc20e"/><stop offset="1" stop-color="#f7861c"/>
      </linearGradient>
    </defs>
    <rect width="678" height="242" fill="var(--panel-navy)"/>
    <polygon points="0,10 323,0 240,242 60,242" fill="var(--navy-deep)"/>
    <g font-family="Anton, sans-serif">
      <text x="59" y="50" fill="#fff" font-size="33" textLength="163" lengthAdjust="spacingAndGlyphs">THE MORE YOU</text>
      <text x="59" y="119" fill="url(#goldFill)" font-size="80" textLength="163" lengthAdjust="spacingAndGlyphs">REFER</text>
      <text x="59" y="149" fill="#fff" font-size="33" textLength="163" lengthAdjust="spacingAndGlyphs">THE MORE YOU</text>
      <text x="59" y="229" fill="url(#goldFill)" font-size="88" textLength="163" lengthAdjust="spacingAndGlyphs">EARN</text>
    </g>
  </svg>
  <div class="abs money-photo" role="img" aria-label="Photo of spread hundred-dollar bills with letter tiles spelling CASH FLOW"></div>

  <h2 class="abs how-title"><span class="how-title__a">HOW IT</span><span class="how-title__b">WORK</span></h2>

  <div class="step" style="left:171px">
    <div class="step__photo" role="img" aria-label="Photo of drying fans and dehumidifiers in a room" style="background:linear-gradient(120deg,#3a8fbf,#a9c2cc 60%,#6b5b4f)"></div>
    <div class="step__title">REFER FLOOD, MOLD &amp;<br>CONSTRUCTION JOBS:</div>
    <div class="step__body">It's Simple to Refer 24/7:<br>Call, Text or Book Online.</div>
  </div>
  <div class="step" style="left:336px">
    <div class="step__photo" role="img" aria-label="Photo of a contractor with a clipboard in front of a house" style="background:linear-gradient(180deg,#b9d3ea,#e8ecef 45%,#6f8a5c)"></div>
    <div class="step__title">WE TAKE CARE OF<br>EVERYTHING:</div>
    <div class="step__body">We Schedule a Free Estimate.<br>If Approved, You Get Paid</div>
  </div>
  <div class="step" style="left:501px">
    <div class="step__photo" role="img" aria-label="Yellow road sign reading Get Paid to Share against a blue sky" style="background:linear-gradient(180deg,#5e9fd8,#cfe2f1 70%,#f1d21a)"></div>
    <div class="step__title">EVERYBODY BENEFITS<br>FROM REFERRALS</div>
    <div class="step__body">We Provide Expert Quality<br>Work for Affordable Price.</div>
  </div>

  <div class="abs refer-row">
    <div class="refer-row__label">REFER</div>
    <div class="refer-row__items">
      <span><svg class="tick" viewBox="0 0 12 12"><circle cx="6" cy="6" r="6" fill="var(--blue)"/><polyline points="3,6 5.2,8.2 9,4" fill="none" stroke="#fff" stroke-width="1.5"/></svg>FLOODS</span>
      <span><svg class="tick" viewBox="0 0 12 12"><circle cx="6" cy="6" r="6" fill="var(--blue)"/><polyline points="3,6 5.2,8.2 9,4" fill="none" stroke="#fff" stroke-width="1.5"/></svg>REMODELS</span>
      <span><svg class="tick" viewBox="0 0 12 12"><circle cx="6" cy="6" r="6" fill="var(--blue)"/><polyline points="3,6 5.2,8.2 9,4" fill="none" stroke="#fff" stroke-width="1.5"/></svg>RENOVATIONS</span>
      <span><svg class="tick" viewBox="0 0 12 12"><circle cx="6" cy="6" r="6" fill="var(--blue)"/><polyline points="3,6 5.2,8.2 9,4" fill="none" stroke="#fff" stroke-width="1.5"/></svg>REPAIRS</span>
    </div>
  </div>

  <div class="abs contact-bar">
    <svg class="abs" style="left:0;top:0" width="678" height="42">
      <polygon points="0,3 270,3 296,42 0,42" fill="var(--blue-bar)"/>
      <polyline points="270,3 294,40" fill="none" stroke="var(--navy)" stroke-width="3"/>
    </svg>
    <span class="contact-bar__cta">CALL, TEXT OR BOOK ONLINE</span>
    <span class="contact-bar__phone">858-471-6093</span>
    <span class="contact-bar__sep"></span>
    <span class="contact-bar__web">www.BrightlaneRenovate.com</span>
  </div>
</section>

</body>
</html>
```